Can you make a cool and versatile Tarn Meridian Powerpoint template?
See www.tarnmeridian-example.co.uk and http://www.examplenet.invalid/company/tarn-meridian-ltd/ (on the right) to see how the logos are currently used - with interchangeably white and black backgrounds.
Target Market(s)
Marketing managers, product managers in HR technology, HR consultants
Industry/Entity Type
It Company
Font styles to use
Sans Serif
Requirements
Must have
- Master slide design, fonts, color theme, etc. Ideally two variations - one with white background (using colorful logo), one with a darker background (using black/white logo).

```html
<!DOCTYPE html>
<html lang="en">
<head>
<meta charset="utf-8">
<title>Tarn Meridian Ltd – Title Slide</title>
<link rel="stylesheet" href="https://fonts.googleapis.com/css2?family=Mulish:wght@400&display=swap">
<style>
  :root {
    --page: #ffffff;
    --band: #000000;
    --band-text: #ffffff;
    --ink: #1c1c1c;
    --link-blue: #2b3f8c;
    --accent: #f08a1c;
    --photo-light: #ffc44a;
    --photo-mid: #e98416;
    --photo-deep: #8a3a05;
    --photo-dark: #3a1503;
  }
  * { margin: 0; padding: 0; box-sizing: border-box; }
  html, body {
    width: 1200px;
    height: 912px;
    overflow: hidden;
    background: var(--page);
  }
  .slide {
    position: relative;
    width: 1200px;
    height: 912px;
    background: var(--page);
    font-family: "Mulish", Arial, sans-serif;
    color: var(--ink);
  }
  .hero-photo {
    position: absolute;
    left: 0; top: 0;
    width: 1200px;
    height: 270px;
    display: block;
  }
  .title-band {
    position: absolute;
    left: 0; top: 270px;
    width: 1200px;
    height: 130px;
    background: var(--band);
  }
  .company-title {
    position: absolute;
    left: 63px;
    top: 44px;
    font-size: 29px;
    font-weight: 400;
    color: var(--band-text);
  }
  .brand-row {
    position: absolute;
    left: 767px;
    top: 574px;
    display: flex;
    align-items: center;
    gap: 16px;
  }
  .brand-dot {
    display: block;
    width: 30px;
    height: 30px;
    flex: none;
  }
  .brand-name {
    font-size: 38px;
    font-weight: 400;
    color: var(--ink);
    line-height: 1;
    white-space: nowrap;
  }
  .brand-url {
    position: absolute;
    left: 824px;
    top: 632px;
    font-size: 19px;
    font-weight: 400;
    color: var(--link-blue);
  }
  .contact {
    position: absolute;
    left: 46px;
    top: 680px;
    font-size: 19px;
    line-height: 25.5px;
    font-style: normal;
    color: var(--ink);
  }
  .contact .address { text-transform: uppercase; }
  .contact .lines { margin-top: 25px; }
</style>
</head>
<body>
  <main class="slide">
    <svg class="hero-photo" viewBox="0 0 1200 270" role="img" aria-label="Warm sunlit photograph: a hand holding a stem of grass against glowing golden bokeh">
      <defs>
        <linearGradient id="heroWarm" x1="0" y1="1" x2="1" y2="0">
          <stop offset="0" stop-color="#3a1503"/>
          <stop offset="0.3" stop-color="#8a3a05"/>
          <stop offset="0.6" stop-color="#e98416"/>
          <stop offset="1" stop-color="#ffc44a"/>
        </linearGradient>
        <radialGradient id="heroGlow" cx="0.72" cy="0.3" r="0.55">
          <stop offset="0" stop-color="#ffd76a" stop-opacity="0.75"/>
          <stop offset="1" stop-color="#ffd76a" stop-opacity="0"/>
        </radialGradient>
      </defs>
      <rect width="1200" height="270" fill="url(#heroWarm)"/>
      <rect width="1200" height="270" fill="url(#heroGlow)"/>
    </svg>

    <section class="title-band">
      <h1 class="company-title">Tarn Meridian Ltd</h1>
    </section>

    <div class="brand-row">
      <svg class="brand-dot" viewBox="0 0 30 30" aria-hidden="true">
        <circle cx="15" cy="15" r="15" fill="var(--accent)"/>
      </svg>
      <span class="brand-name">Tarn Meridian</span>
    </div>
    <div class="brand-url">www.tarnmeridian-example.co.uk</div>

    <address class="contact">
      <div class="address">
        Studio B3<br>
        Larchmont Works<br>
        14 Fenwick Lane<br>
        London SE9 4QX
      </div>
      <div class="lines">
        Phone: +44 (0) 7000 000123<br>
        Email: ellis.harrow[@]tarnmeridian-example.co.uk
      </div>
    </address>
  </main>
</body>
</html>
```